Rack Card for Bright Meadow Dog Training

I love the logo you designed for me a while back (I had it updated and have the new files).

I need a rack card designed, 2 sided.

One side will be Bright Meadow Dog Training (my general dog training business)

The other side will be my Deaf and Blind Dog Training Business speciality.

Both sides Full Color/4 color

3.5 x 8.5 inches

I can provide photos and text accordingly.

Let me know the estimated price and Turn around time.

```html
<!DOCTYPE html>
<html lang="en">
<head>
<meta charset="utf-8">
<title>Bright Meadow Dog Training – Rack Card</title>
<link href="https://fonts.googleapis.com/css2?family=Poppins:wght@400;500;600;700;800&display=swap" rel="stylesheet">
<style>
  :root{
    --charcoal:#3a3a35;
    --cream:#efebdd;
    --orange:#e09a12;
    --white:#ffffff;
    --stage:#e2e2e2;
    --ink:#2f2f2b;
  }
  *{box-sizing:border-box;margin:0;padding:0}
  html,body{width:931px;height:1200px;overflow:hidden}
  body{background:var(--stage);font-family:"Poppins",sans-serif;color:var(--ink);position:relative}

  .card{position:absolute;top:115px;width:400px;height:971px;overflow:hidden;background:var(--white);box-shadow:0 6px 14px rgba(0,0,0,.18)}
  .card--services{left:45px}
  .card--speciality{left:486px}
  .card__shapes{position:absolute;inset:0;width:400px;height:971px}
  .abs{position:absolute}

  .tagline{top:33px;left:0;width:100%;text-align:center;color:var(--white);font-size:13.5px;letter-spacing:3px;font-weight:500}
  .tagline strong{color:var(--orange);font-weight:700}

  .headline{font-weight:800;font-size:29px;line-height:28px;color:var(--charcoal);letter-spacing:.2px}
  .headline .amp{font-weight:400}
  .pill{background:var(--orange);color:var(--white);font-weight:500;letter-spacing:6px;text-align:center;border-radius:5px;font-size:16px;line-height:29px;height:29px}

  .brand{top:110px;left:268px;width:118px;text-align:center;font-weight:500;font-size:19px;line-height:23px;color:var(--charcoal)}
  .brand__dot{display:block;width:14px;height:14px;border-radius:50%;background:var(--charcoal);margin:0 auto 8px}

  .checklist{top:242px;left:35px;list-style:none}
  .checklist li{position:relative;padding-left:21px;font-weight:600;font-size:15.5px;line-height:21.2px;color:var(--charcoal)}
  .checklist li::before{content:"";position:absolute;left:0;top:5px;width:13px;height:13px;border-radius:50%;background:var(--orange)}
  .checklist li::after{content:"";position:absolute;left:4px;top:7.5px;width:3.5px;height:6px;border:solid var(--white);border-width:0 2px 2px 0;transform:rotate(45deg)}

  .photo{position:absolute;border:7px solid var(--white);box-shadow:0 0 0 5px #f1efe9}
  .blob-a{border-radius:48% 52% 44% 56% / 55% 45% 55% 45%}
  .blob-b{border-radius:55% 45% 50% 50% / 45% 55% 45% 55%}
  .cutout{position:absolute;border-radius:45% 55% 40% 60% / 50% 45% 55% 50%}

  .label{font-size:22px;line-height:23px;color:var(--charcoal);font-weight:400}
  .label b{display:block;color:var(--orange);font-weight:700}

  .feature{width:180px}
  .feature--right{width:196px}
  .feature h3{color:var(--orange);font-weight:600;font-size:14.5px;line-height:17px;margin-bottom:1px;white-space:nowrap}
  .feature p{font-size:11px;line-height:12.4px;color:var(--ink);width:178px}

  .contact{left:34px;top:886px;color:var(--white);width:150px}
  .contact small{display:block;color:var(--orange);font-size:8.5px;line-height:9px;font-weight:500}
  .contact .phone{font-size:15px;line-height:17px;font-weight:600;margin-bottom:6px;display:flex;align-items:center;gap:2px}
  .contact .phone svg,.contact .mail svg{flex:none}
  .contact .mail{font-size:12.5px;line-height:14px;display:flex;align-items:center;gap:4px;margin-top:-3px;white-space:nowrap}
  .consult{left:192px;top:925px;color:var(--white);border-left:1px solid var(--white);padding-left:4px}
  .consult p{font-size:9.5px;line-height:11px}
  .consult p em{font-style:normal;color:var(--orange);font-weight:600}
  .consult strong{display:block;font-size:15.5px;line-height:19px;font-weight:700;white-space:nowrap}
</style>
</head>
<body>

<!-- Side A: general services -->
<section class="card card--services">
  <svg class="card__shapes" viewBox="0 0 400 971" aria-hidden="true">
    <path d="M0 0H400V420C335 440 280 402 205 414C125 426 60 452 0 430Z" fill="var(--cream)"/>
    <path d="M0 0H400V48C300 95 120 100 0 62Z" fill="var(--charcoal)"/>
    <path d="M0 971V868C90 885 170 878 225 858C295 832 345 826 400 818V971Z" fill="var(--charcoal)"/>
  </svg>

  <p class="abs tagline"><strong>LEADING</strong> DOG TRAINING INDUSTRY</p>

  <h1 class="abs headline" style="top:105px;left:34px">PRIVATE DOG<br>TRAINING <span class="amp">&amp;</span><br>BEHAVIORAL</h1>
  <div class="abs pill" style="top:193px;left:35px;width:176px">SERVICES</div>

  <div class="abs brand"><span class="brand__dot"></span>Bright<br>Meadow</div>

  <ul class="abs checklist">
    <li>Puppy Training</li>
    <li>House Breaking</li>
    <li>Leash Training</li>
    <li>Obedience</li>
    <li>Rescue Dog Training</li>
    <li>Separation Anxiety</li>
    <li>Socialization</li>
  </ul>

  <div class="cutout" role="img" aria-label="Photo of a seated beagle on a leash" style="left:228px;top:213px;width:180px;height:222px;background:radial-gradient(circle at 45% 40%,#d9a56c,#a8683a 60%,#efe6d8)"></div>

  <div class="photo blob-a" role="img" aria-label="Photo of beagle puppies lying together" style="left:45px;top:440px;width:150px;height:140px;background:linear-gradient(160deg,#4b4b4b,#7a5a3c 60%,#e8e2da)"></div>
  <p class="abs label" style="left:224px;top:478px"><b>Puppy</b>Training</p>

  <p class="abs label" style="left:59px;top:590px"><b>Rescue</b>Dogs</p>
  <div class="photo blob-b" role="img" aria-label="Photo of a person hugging a rescued dog" style="left:212px;top:545px;width:148px;height:138px;background:linear-gradient(150deg,#5a6a6a,#b06a35 55%,#3b3b3f)"></div>

  <div class="photo blob-b" role="img" aria-label="Photo of an adult dog against a brick wall" style="left:45px;top:638px;width:145px;height:140px;background:linear-gradient(160deg,#c76a35,#a3592a 55%,#5a3a22)"></div>
  <p class="abs label" style="left:224px;top:683px"><b>Adult Dog</b>Training</p>

  <p class="abs label" style="left:59px;top:784px"><b>Behavioral</b>Issues</p>
  <div class="photo blob-a" role="img" aria-label="Photo of a dog chewing a shoe indoors" style="left:212px;top:738px;width:148px;height:140px;background:linear-gradient(160deg,#8c8f92,#4a4544 50%,#e6e4e0)"></div>

  <div class="abs contact">
    <small>LOS ANGELES</small>
    <div class="phone"><svg width="11" height="11" viewBox="0 0 24 24"><path d="M6.6 10.8a15 15 0 0 0 6.6 6.6l2.2-2.2a1 1 0 0 1 1-.25 11.4 11.4 0 0 0 3.6.57 1 1 0 0 1 1 1V20a1 1 0 0 1-1 1A17 17 0 0 1 3 4a1 1 0 0 1 1-1h3.5a1 1 0 0 1 1 1c0 1.25.2 2.45.57 3.570a1 1 0 0 1-.25 1Z" fill="var(--orange)"/></svg>(310) 555-0142</div>
    <small>ORANGE COUNTY</small>
    <div class="phone"><svg width="11" height="11" viewBox="0 0 24 24"><path d="M6.6 10.8a15 15 0 0 0 6.6 6.6l2.2-2.2a1 1 0 0 1 1-.25 11.4 11.4 0 0 0 3.6.57 1 1 0 0 1 1 1V20a1 1 0 0 1-1 1A17 17 0 0 1 3 4a1 1 0 0 1 1-1h3.5a1 1 0 0 1 1 1c0 1.25.2 2.45.57 3.57a1 1 0 0 1-.25 1Z" fill="var(--orange)"/></svg>(714) 555-0187</div>
    <div class="mail"><svg width="9" height="7" viewBox="0 0 18 13"><rect width="18" height="13" rx="1" fill="var(--orange)"/><path d="M1 1l8 6 8-6" stroke="var(--charcoal)" stroke-width="1.5" fill="none"/></svg>bmeadow@mail.com</div>
  </div>
  <div class="abs consult">
    <p>Schedule a <em>FREE 15 Minute</em><br>Phone Consultation with Lead Trainer</p>
    <strong>Dana Whitfield Moreno</strong>
  </div>
</section>

<!-- Side B: deaf & blind speciality -->
<section class="card card--speciality">
  <svg class="card__shapes" viewBox="0 0 400 971" aria-hidden="true">
    <path d="M0 0H400V325C330 332 265 312 190 330C120 347 60 322 0 300Z" fill="var(--cream)"/>
    <path d="M0 0H400V48C300 95 120 100 0 62Z" fill="var(--charcoal)"/>
    <path d="M0 971V868C90 885 170 878 225 858C295 832 345 826 400 818V971Z" fill="var(--charcoal)"/>
  </svg>

  <p class="abs tagline"><strong>LEADING</strong> DOG TRAINING INDUSTRY</p>

  <div class="cutout" role="img" aria-label="Photo of a large senior dog lying down" style="left:0;top:72px;width:200px;height:250px;background:radial-gradient(circle at 50% 45%,#d38c45,#b66d2c 55%,#efe6d8)"></div>

  <h1 class="abs headline" style="top:105px;left:196px">DEAF <span class="amp">&amp;</span><br>BLIND DOG<br>TRAINING<br>BUSINESS</h1>
  <div class="abs pill" style="top:223px;left:197px;width:176px">SPECIALITY</div>

  <div class="photo blob-a" role="img" aria-label="Photo of a deaf dog on a beach" style="left:28px;top:325px;width:148px;height:143px;background:linear-gradient(160deg,#9fb6c8,#7a5c44 55%,#ece7e0)"></div>
  <div class="abs feature feature--right" style="left:198px;top:334px">
    <h3>Deaf Dog Training</h3>
    <p>Deaf dogs can easily be trained using hand signals.<br>We owe it to our dogs to teach them how to behave, and that the world is a safe place. A dog with special needs is no exception.<br>Training a dog that is deaf can come with it challenges.</p>
  </div>

  <div class="abs feature" style="left:33px;top:490px">
    <h3>Blind Dog Training</h3>
    <p>Deaf dogs can easily be trained using hand signals.<br>We owe it to our dogs to teach them how to behave, and that the world is a safe place. A dog with special needs is no exception.<br>Training a dog that is deaf can come with it challenges.</p>
  </div>
  <div class="photo blob-b" role="img" aria-label="Photo of a blind golden retriever" style="left:220px;top:482px;width:150px;height:143px;background:radial-gradient(circle at 50% 50%,#b8743d,#8a4e28 60%,#6a3a1e)"></div>

  <div class="photo blob-b" role="img" aria-label="Photo of a white dog wearing a deaf and blind vest" style="left:32px;top:642px;width:148px;height:140px;background:linear-gradient(160deg,#6f8a3e,#e9ecef 55%,#7a6a55)"></div>
  <div class="abs feature feature--right" style="left:198px;top:643px">
    <h3>Deaf / Blind Dog Training</h3>
    <p>Deaf/Blind dogs can easily be trained using touch and tactile cues.<br>We owe it to our dogs to teach them how to behave, to know their surroundings even when their sight and hearing is lost, &amp; that the world is a safe place.</p>
  </div>

  <div class="cutout" role="img" aria-label="Photo of a bulldog standing" style="left:262px;top:780px;width:80px;height:125px;background:linear-gradient(180deg,#d9b58a,#f2ede6 55%,#c9a57a)"></div>

  <div class="abs contact">
    <small>LOS ANGELES</small>
    <div class="phone"><svg width="11" height="11" viewBox="0 0 24 24"><path d="M6.6 10.8a15 15 0 0 0 6.6 6.6l2.2-2.2a1 1 0 0 1 1-.25 11.4 11.4 0 0 0 3.6.57 1 1 0 0 1 1 1V20a1 1 0 0 1-1 1A17 17 0 0 1 3 4a1 1 0 0 1 1-1h3.5a1 1 0 0 1 1 1c0 1.25.2 2.45.57 3.57a1 1 0 0 1-.25 1Z" fill="var(--orange)"/></svg>(310) 555-0142</div>
    <small>ORANGE COUNTY</small>
    <div class="phone"><svg width="11" height="11" viewBox="0 0 24 24"><path d="M6.6 10.8a15 15 0 0 0 6.6 6.6l2.2-2.2a1 1 0 0 1 1-.25 11.4 11.4 0 0 0 3.6.57 1 1 0 0 1 1 1V20a1 1 0 0 1-1 1A17 17 0 0 1 3 4a1 1 0 0 1 1-1h3.5a1 1 0 0 1 1 1c0 1.25.2 2.45.57 3.57a1 1 0 0 1-.25 1Z" fill="var(--orange)"/></svg>(714) 555-0187</div>
    <div class="mail"><svg width="9" height="7" viewBox="0 0 18 13"><rect width="18" height="13" rx="1" fill="var(--orange)"/><path d="M1 1l8 6 8-6" stroke="var(--charcoal)" stroke-width="1.5" fill="none"/></svg>bmeadow@mail.com</div>
  </div>
  <div class="abs consult">
    <p>Schedule a <em>FREE 15 Minute</em><br>Phone Consultation with Lead Trainer</p>
    <strong>Dana Whitfield Moreno</strong>
  </div>
</section>

</body>
</html>
```